Flyer / Small Safety "Poster" (A4 or 8.5x11" paper)

We're looking to create a series of safety signs for woodworkers to print on home printers using standard sized paper (A4 or 8.5x11" depending on where they are), or possibly to have printed on 17x22" paper.
Currently we want only the first one, but keep in mind that all should work together.
They need: Simple graphic. Bold Text. Company logo. Use company colors (orange, black, white.)
To begin, we will start with a single sign for hearing protection. Graphic or clip art to portray either ear plugs or ear-muff design. Text to say, "Hearing Protection is a Sound Investment."

Target Market(s)

USA Woodworkers & CNC Machinists - Male, 20-65 years old

Font styles to use
Sans Serif

Colors
f37122

Requirements
Must have
• Client logo
Nice to have
• Use client colors of black, white, & orange

```html
<!DOCTYPE html>
<html lang="en">
<head>
<meta charset="utf-8">
<title>Hearing Protection Is A Sound Investment</title>
<link href="https://fonts.googleapis.com/css2?family=Anton&family=Josefin+Sans:wght@300&family=Open+Sans:wght@400;700&display=swap" rel="stylesheet">
<style>
  :root{
    --orange:#f39a12;
    --orange-deep:#e88a0a;
    --black:#0b0b0b;
    --paper:#f1f1f0;
    --white:#ffffff;
    --stage:#4b535e;
    --photo-light:#e6dccd;
    --photo-mid:#b89a78;
    --photo-dark:#6a5040;
  }
  *{margin:0;padding:0;box-sizing:border-box}
  html,body{width:1200px;height:900px;overflow:hidden;background:var(--stage)}
  .flyer{
    position:absolute;left:283px;top:40px;width:634px;height:820px;
    background:var(--paper);overflow:hidden;
  }
  .block{position:absolute;background:var(--orange)}
  .block--top{left:22px;top:160px;width:300px;height:140px}
  .block--bottom{left:120px;top:652px;width:360px;height:130px}
  .check{position:absolute;width:40px;height:40px}
  .check--orange{background:var(--orange)}
  .check--white{background:var(--white)}
  .bar{position:absolute;background:var(--black)}
  .bar--top{left:290px;top:160px;width:344px;height:16px}
  .bar--bottom{left:470px;top:555px;width:164px;height:20px}
  .photo{
    position:absolute;left:290px;top:176px;width:344px;height:379px;
    background:
      radial-gradient(ellipse 40% 35% at 55% 35%, var(--photo-mid), transparent 70%),
      linear-gradient(160deg,var(--photo-light) 0%,#d3c3ad 45%,var(--photo-mid) 80%,var(--photo-dark) 100%);
  }
  .photo-tint{
    position:absolute;left:60px;top:312px;width:340px;height:328px;
    background:linear-gradient(165deg,#f0a432 0%,var(--orange-deep) 55%,#c9740a 100%);
    opacity:.95;
  }
  .brand{
    position:absolute;right:36px;top:30px;text-align:right;
    font-family:"Open Sans",sans-serif;color:var(--black);
  }
  .brand__name{font-weight:700;font-size:26px;letter-spacing:1px;line-height:1;display:flex;align-items:center;gap:8px;justify-content:flex-end}
  .brand__mark{width:16px;height:16px;background:var(--black)}
  .brand__tagline{font-size:11px;margin-top:7px;font-weight:400;line-height:1}
  .headline{
    position:absolute;left:76px;top:410px;
    font-family:"Anton",sans-serif;color:var(--white);text-transform:uppercase;
    font-size:52px;font-weight:400;letter-spacing:1px;
  }
  .headline__line{display:block;height:56px;line-height:56px;white-space:nowrap}
  .headline__soft{
    font-family:"Josefin Sans",sans-serif;font-weight:300;font-size:54px;letter-spacing:2px;
  }
</style>
</head>
<body>
  <main class="flyer">
    <div class="photo" role="img" aria-label="Photo of a woodworker wearing red earmuffs and clear safety glasses, working at a bench"></div>
    <div class="photo-tint" role="img" aria-label="Orange-tinted close-up of a power tool in the workshop"></div>

    <div class="block block--top"></div>
    <div class="check check--white" style="left:242px;top:80px"></div>
    <div class="check check--orange" style="left:282px;top:80px"></div>
    <div class="check check--orange" style="left:242px;top:120px"></div>
    <div class="check check--white" style="left:282px;top:120px"></div>
    <div class="check check--white" style="left:242px;top:160px"></div>

    <div class="bar bar--top"></div>
    <div class="bar bar--bottom"></div>

    <div class="block block--bottom"></div>
    <div class="check check--orange" style="left:80px;top:702px"></div>
    <div class="check check--white" style="left:120px;top:702px"></div>
    <div class="check check--white" style="left:80px;top:742px"></div>
    <div class="check check--orange" style="left:80px;top:782px"></div>
    <div class="check check--white" style="left:120px;top:782px"></div>

    <header class="brand">
      <div class="brand__name"><span class="brand__mark"></span>GRAINLINE SUPPLY</div>
      <div class="brand__tagline">Sharp bits and blades for every shop!</div>
    </header>

    <h1 class="headline">
      <span class="headline__line">Hearing</span>
      <span class="headline__line">Protection</span>
      <span class="headline__line">Is A <span class="headline__soft">Sound</span></span>
      <span class="headline__line">Investment</span>
    </h1>
  </main>
</body>
</html>
```